Buch-/E-Book-Cover für Buch über die Ausdrucksweise
Zielgruppe
Deutsche Version
Ich bin Autor und habe ich Buch über 'Ausdrucksweise verbessern' geschrieben. Das Buch steht aktuell zum Verkauf. Allerdings gefällt mir das Cover nicht gut. Deswegen möchte ich gerne ein neues Cover erstellen lassen. Der Haupttitel lautet 'Worte wirken weiter' und der Untertitel: 'Klarer reden & Sprachgefühl stärken: Das Übungsbuch mit anschaulichen Fällen, wie Sie in jeder Unterhaltung mit Redekunst und Stilsicherheit' Autor ist 'Jonas Brettfeld'
English Version
I am an author and I have written a book on 'Improving Expression'. The book is currently for sale. However, I don't like the cover very much. Therefore, I would like to have a new cover created. The main title is 'Words carry further = Worte wirken weiter' and the subtitle is: 'Speak clearly & sharpen your style: The hands-on workbook with vivid cases showing how to apply eloquence and verbal confidence in every discussion' = 'Klarer reden & Sprachgefühl stärken: Das Übungsbuch mit anschaulichen Fällen, wie Sie in jeder Unterhaltung mit Redekunst und Stilsicherheit'. Author is 'Jonas Brettfeld'.
Aufgabenstellung
Ich habe das aktuelle Cover beigefügt. Mir gefällt die Symbolik des aktuellen Covers noch nicht. Ich denke mit dem Titel 'Worte wirken weiter' kann man noch mehr herausholen, indem man eine bessere Symbolik verwendet. Wichtig ist, dass der potenzielle Kunde sofort die Symbolik mit dem Inhalt assoziiert.
Die Konkurrenzbücher auf Lesora können gute Hinweise sein. Allerdings sollte das neue Cover hier explizit herausstechen: https://www.lesora-shop.de/s?k=ausdrucksweise+verbessern&i=stripbooks&sprefix=ausdrucksw%2Cstripbooks%2C77&ref=nb_sb_ss_ts-doa-p_1_10
Folgende Punkte sind wichtig:
- Haupttitel muss gut lesbar sein. (Untertitel ist unwichtig)
- 'Praxisguide' sollte herausstechen
- Es sollte erkenntlich gemacht werden, dass das Buch ein Hörbuch enthält
Ich habe die Covervorlage mit dem passendem Format hinzugefügt.
English Version:
I have attached the current cover. I don't like the symbolism of the current cover yet. I think with the title 'Words carry further' you can get more out of it by using better symbolism. It is important that the potential customer immediately associates the symbolism with the content.
Competitor books on Lesora can be good clues. However, the new cover should explicitly stand out here: https://www.lesora-shop.de/s?k=ausdrucksweise+improve&i=stripbooks&sprefix=expressionsw%2Cstripbooks%2C77&ref=nb_sb_ss_ts-doa-p_1_10
The following points are important:
- Main title must be easy to read. (Subtitle is not important).
- The cover and the title must be recognizable even in very small format (thumb size - see lesora)
- 'Praxisguide should stand out
- It should be made recognizable that the book contains an audio book 'Inkl.Hörbuch'
I have added the cover template with the appropriate format.

```html
<!DOCTYPE html>
<html lang="de">
<head>
<meta charset="utf-8">
<title>Worte wirken weiter – Jonas Brettfeld</title>
<link rel="stylesheet" href="https://fonts.googleapis.com/css2?family=Caveat+Brush&family=Oswald:wght@300;400;500&family=Arimo&family=Alfa+Slab+One&display=swap">
<style>
  :root {
    --wine: #951d31;
    --coral: #e33c5a;
    --white: #ffffff;
    --ink: #0b0b0b;
    --grey: #e4e4e4;
    --signal: #e0392b;
  }
  html, body { margin: 0; padding: 0; overflow: hidden; }
  .cover {
    position: relative;
    width: 825px;
    height: 1200px;
    background: var(--wine);
    overflow: hidden;
    color: var(--white);
  }
  .brackets { position: absolute; inset: 0; }
  .quote {
    position: absolute;
    font-family: "Alfa Slab One", serif;
    color: var(--white);
    line-height: 1;
    font-size: 330px;
  }
  .quote--open { left: 140px; top: 0px; transform: rotate(-6deg); }
  .quote--close { left: 488px; top: 725px; transform: rotate(4deg); }
  .title {
    position: absolute;
    left: 200px;
    width: 465px;
    top: 250px;
    margin: 0;
    text-align: center;
    font-family: "Caveat Brush", cursive;
    font-weight: 400;
    line-height: 1;
  }
  .title__big { display: block; font-size: 136px; }
  .title__small { display: block; font-size: 70px; margin: 8px 0 6px; }
  .subtitle {
    position: absolute;
    left: 200px;
    width: 465px;
    top: 630px;
    margin: 0;
    text-align: center;
    font-family: "Oswald", sans-serif;
    font-weight: 400;
    font-size: 36px;
    line-height: 1.38;
  }
  .band {
    position: absolute;
    left: 0;
    top: 990px;
    width: 825px;
    height: 96px;
    background: var(--ink);
  }
  .band__label {
    position: absolute;
    left: 162px;
    top: 4px;
    margin: 0;
    font-family: "Oswald", sans-serif;
    font-weight: 500;
    font-size: 70px;
    line-height: 88px;
    letter-spacing: 1px;
  }
  .audio-badge { position: absolute; left: 630px; top: 878px; width: 180px; height: 150px; }
  .audio-badge__label {
    position: absolute;
    left: 620px;
    top: 1020px;
    margin: 0;
    font-family: "Caveat Brush", cursive;
    font-size: 38px;
    transform: rotate(7deg);
    white-space: nowrap;
  }
  .tagline {
    position: absolute;
    left: 0;
    width: 825px;
    top: 1087px;
    margin: 0;
    text-align: center;
    font-family: "Oswald", sans-serif;
    font-weight: 300;
    font-size: 22px;
    line-height: 34px;
    letter-spacing: -0.3px;
  }
  .author {
    position: absolute;
    left: 0;
    width: 825px;
    top: 1140px;
    margin: 0;
    text-align: center;
    font-family: "Arimo", sans-serif;
    font-size: 28px;
    color: var(--grey);
    letter-spacing: 1px;
  }
</style>
</head>
<body>
<main class="cover">
  <svg class="brackets" width="825" height="1200" viewBox="0 0 825 1200" aria-hidden="true">
    <path fill="var(--coral)" d="M88 178 H228 V262 H200 V762 H253 V890 H88 Z"/>
    <path fill="var(--coral)" d="M636 119 H765 V791 H620 V703 H672 V217 H636 Z"/>
  </svg>

  <span class="quote quote--open" aria-hidden="true">“</span>
  <span class="quote quote--close" aria-hidden="true">”</span>

  <h1 class="title">
    <span class="title__big">Worte</span>
    <span class="title__small">wirken</span>
    <span class="title__big">weiter</span>
  </h1>

  <p class="subtitle">Klarer reden &amp;<br>Sprachgefühl stärken</p>

  <div class="band">
    <p class="band__label">Das Übungsbuch</p>
  </div>

  <svg class="audio-badge" viewBox="0 0 180 150" aria-hidden="true">
    <path d="M22 120 V82 A68 68 0 0 1 158 82 V120" fill="none" stroke="var(--white)" stroke-width="14" stroke-linecap="round"/>
    <rect x="4" y="92" width="34" height="40" rx="14" fill="var(--white)"/>
    <rect x="142" y="92" width="34" height="40" rx="14" fill="var(--white)"/>
    <line x1="52" y1="70" x2="46" y2="150" stroke="var(--white)" stroke-width="9" stroke-linecap="round"/>
    <line x1="128" y1="70" x2="134" y2="150" stroke="var(--white)" stroke-width="9" stroke-linecap="round"/>
    <circle cx="90" cy="112" r="26" fill="var(--signal)"/>
    <path d="M81 99 L104 112 L81 125 Z" fill="var(--white)"/>
  </svg>
  <p class="audio-badge__label">mit Hörbuch</p>

  <p class="tagline">mit anschaulichen Fällen, wie Sie in jeder Unterhaltung mit Redekunst und Stilsicherheit überzeugen</p>

  <p class="author">Jonas Brettfeld</p>
</main>
</body>
</html>
```